Printer Cartridges Supplier Namecard

Attached is my company logo and the design of my current namecard. I would like to have a more special look for it. Can have a little cuteness too rather than those normal standard feel. I'm a supplier mainly dealing with original and compatible printer toner cartridges, some other products like paper supplies as well.

Target Market(s)

Companies, businesses, corporates

Industry/Entity Type

It Company

Contact Information for Business Card

Logo, name, contact, address, supplies and maybe a slogan

Colors
85cae6
33a6d7
3176b5
0255a3
0792cd
85abd2

Requirements
Must have
• Logo, name, contact and address basic details.
• Must include some pictures, not just rearrange what I'm currently having.
Nice to have
• Be creative and bold, a diiferent traditional feel.

```html
<!DOCTYPE html>
<html lang="en">
<head>
<meta charset="utf-8">
<title>tonerbay – Namecard</title>
<link rel="stylesheet" href="https://fonts.googleapis.com/css2?family=Roboto:wght@400;500&family=Roboto+Condensed:wght@700&display=swap">
<style>
  :root {
    --backdrop: #e8e6e3;
    --card-white: #f7f7f6;
    --brand-blue: #63b5e5;
    --picture-tone: #e9f5fc;
    --text-grey: #555555;
    --text-dark: #444444;
    --white: #ffffff;
  }
  html, body {
    margin: 0;
    padding: 0;
    width: 1200px;
    height: 960px;
    overflow: hidden;
    background: var(--backdrop);
    font-family: "Roboto", Arial, sans-serif;
  }
  .canvas {
    position: relative;
    width: 1200px;
    height: 960px;
  }
  .card {
    position: absolute;
    width: 600px;
    height: 342px;
    box-sizing: border-box;
  }
  .card--front {
    left: 302px;
    top: 129px;
    background: var(--card-white);
  }
  .card--back {
    left: 299px;
    top: 488px;
    background: var(--brand-blue);
  }

  /* Front: brand block */
  .brand {
    position: absolute;
    right: 46px;
    top: 40px;
    text-align: right;
  }
  .brand__row {
    display: flex;
    align-items: center;
    justify-content: flex-end;
    gap: 10px;
  }
  .brand__dot {
    width: 22px;
    height: 22px;
    border-radius: 50%;
    background: var(--brand-blue);
  }
  .brand__name {
    font-size: 46px;
    line-height: 1;
    font-weight: 400;
    color: var(--text-grey);
    letter-spacing: 0.5px;
  }
  .brand__tagline {
    margin-top: 3px;
    font-size: 7px;
    line-height: 8px;
    color: var(--text-grey);
  }

  /* Front: person and details */
  .person {
    position: absolute;
    left: 48px;
    top: 130px;
  }
  .person__name {
    margin: 0;
    font-family: "Roboto Condensed", "Arial Narrow", sans-serif;
    font-weight: 700;
    font-size: 20px;
    line-height: 24px;
    color: var(--brand-blue);
  }
  .person__role {
    margin: 1px 0 0;
    font-weight: 500;
    font-size: 15px;
    line-height: 18px;
    color: var(--text-grey);
  }
  .address {
    margin: 9px 0 0;
    font-style: normal;
    font-size: 14.5px;
    line-height: 18px;
    color: var(--text-dark);
  }
  .contacts {
    list-style: none;
    margin: 10px 0 0;
    padding: 0;
    font-size: 14.5px;
    line-height: 18.5px;
    color: var(--text-dark);
  }
  .contacts__item {
    display: flex;
    align-items: center;
    gap: 6px;
  }
  .contacts__icon {
    width: 13px;
    height: 13px;
    fill: var(--brand-blue);
    flex: none;
  }

  /* Back */
  .back-picture {
    position: absolute;
    left: 200px;
    top: 75px;
    width: 200px;
    height: 163px;
    border-radius: 14px;
    background: linear-gradient(180deg, var(--white) 0%, var(--picture-tone) 100%);
  }
  .services {
    position: absolute;
    left: 0;
    right: 0;
    top: 271px;
    margin: 0;
    text-align: center;
    font-size: 15px;
    line-height: 18px;
    color: var(--white);
  }
</style>
</head>
<body>
<main class="canvas">
  <section class="card card--front" aria-label="Namecard front">
    <div class="brand">
      <div class="brand__row">
        <span class="brand__dot"></span>
        <span class="brand__name">tonerbay</span>
      </div>
      <div class="brand__tagline">Compatible printer ink and toner solutions</div>
    </div>

    <div class="person">
      <h1 class="person__name">MAREN TAY</h1>
      <p class="person__role">Sales Executive</p>
      <address class="address">
        57A Harbourline Avenue<br>
        #05-214<br>
        Singapore 530457
      </address>
      <ul class="contacts">
        <li class="contacts__item">
          <svg class="contacts__icon" viewBox="0 0 24 24" aria-hidden="true"><path d="M6.6 10.8c1.4 2.8 3.8 5.1 6.6 6.6l2.2-2.2c.3-.3.7-.4 1-.2 1.1.4 2.3.6 3.6.6.6 0 1 .4 1 1V20c0 .6-.4 1-1 1C10.6 21 3 13.4 3 4c0-.6.4-1 1-1h3.5c.6 0 1 .4 1 1 0 1.3.2 2.5.6 3.6.1.3 0 .7-.2 1z"/></svg>
          HP 9000 4172
        </li>
        <li class="contacts__item">
          <svg class="contacts__icon" viewBox="0 0 24 24" aria-hidden="true"><path d="M2 5h20v14H2z"/><path d="M3 6.2l9 6.3 9-6.3V5H3z" fill="#f7f7f6"/></svg>
          maren@tonerbay.sg
        </li>
        <li class="contacts__item">
          <svg class="contacts__icon" viewBox="0 0 24 24" aria-hidden="true"><circle cx="12" cy="12" r="10"/><path d="M2 12h20M12 2c3 3 3 17 0 20M12 2c-3 3-3 17 0 20" stroke="#f7f7f6" stroke-width="1.5" fill="none"/></svg>
          www.tonerbay.sg
        </li>
      </ul>
    </div>
  </section>

  <section class="card card--back" aria-label="Namecard back">
    <div class="back-picture" role="img" aria-label="Large white printer illustration"></div>
    <p class="services">
      Printer Ink &amp; Toner Cartridges • Original Printer Cartridges<br>
      Paper Products • Printer Maintainence &amp; Repair
    </p>
  </section>
</main>
</body>
</html>
```